Pellowar

We need logo and wesbsite for a software development company based out of Hyderabad, India focused on startups and mid sized companies focused on build a new software products in USA and Europe countires.

Target Market(s)

startup and midsized companies in teh USA and Europe for software product development.

Industry/Entity Type

software development

Coding

Coded - Design and coding required

Number of Pages Required

5+ page

Requirements
Must have
• latest design concepts and very elegant
Nice to have
• each page should have images that reflects the content
Should not have
• too many colors

```html
<!DOCTYPE html>
<html lang="en">
<head>
<meta charset="utf-8">
<title>Pellowar – Software Development</title>
<link href="https://fonts.googleapis.com/css2?family=Lato:wght@400;700;900&family=Montserrat:wght@700;800&display=swap" rel="stylesheet">
<style>
:root{
  --ink:#0a0c13;
  --blue:#1c74e9;
  --blue-light:#3d8df5;
  --text:#4a4d55;
  --muted:#8b8f99;
  --band:#f1f2f5;
  --white:#ffffff;
  --yellow:#f6c21c;
}
*{box-sizing:border-box;margin:0;padding:0}
html,body{width:1200px;height:3360px;overflow:hidden}
body{font-family:'Lato',sans-serif;color:var(--text);background:var(--white);position:relative}
.abs{position:absolute}

/* hero */
.hero{left:0;top:0;width:1200px;height:720px;background:var(--ink)}
.hero-visual{left:0;top:0;width:1200px;height:720px;
  background:radial-gradient(ellipse at 72% 45%,#1e4a9c 0%,#0f2352 30%,rgba(10,12,19,0) 62%),linear-gradient(120deg,#0a0c13 0%,#0d1630 55%,#0a0c13 100%)}
.hero-device{left:620px;top:110px;width:520px;height:420px;border-radius:30px;
  background:radial-gradient(ellipse at 50% 55%,#6fa9ff 0%,#2d62c8 35%,rgba(20,40,90,0) 72%);opacity:.75}
.nav{left:0;top:0;width:1200px;height:80px}
.brand{left:40px;top:16px;font-family:'Montserrat',sans-serif;font-weight:800;font-size:38px;color:var(--white);letter-spacing:-.5px}
.menu{left:440px;top:40px;display:flex;gap:26px;list-style:none;font-size:14px;font-weight:700;color:var(--white);white-space:nowrap}
.menu li.active{border-bottom:2px solid var(--white);padding-bottom:3px}
.btn{display:inline-block;background:var(--blue);color:var(--white);font-weight:700;font-size:14px;letter-spacing:.5px;border-radius:30px;text-transform:uppercase;text-align:center;white-space:nowrap}
.quote{left:960px;top:28px;width:148px;height:44px;line-height:44px}
.hero-title{left:40px;top:216px;font-family:'Montserrat',sans-serif;font-weight:800;font-size:58px;line-height:74px;color:var(--white)}
.hero-title span{color:var(--blue-light)}
.start{left:128px;top:380px;width:148px;height:46px;line-height:46px}
.dots{left:112px;top:522px;display:flex;gap:8px}
.dots i{width:12px;height:12px;border-radius:50%;border:2px solid var(--white)}
.dots i:first-child{background:var(--white)}
.hero-wave{left:0;top:560px;width:1200px;height:180px}
.mouse{left:686px;top:666px;width:46px;height:78px;border-radius:24px;background:var(--yellow);border:4px solid #d9a30a}
.mouse::after{content:"";position:absolute;left:17px;top:12px;width:4px;height:16px;border-radius:2px;background:#8a6506}

/* content */
.band{left:0;width:1200px}
.photo{border-radius:50%;border:10px solid var(--blue);box-shadow:inset 0 0 0 8px var(--white)}
.h2{font-family:'Montserrat',sans-serif;font-weight:800;font-size:40px;color:#14161c;text-transform:uppercase;white-space:nowrap}
.text-block{display:flex;flex-direction:column;align-items:flex-start}
.text-block.right{align-items:flex-end;text-align:right}
.copy{font-size:14px;line-height:21px;color:var(--text)}
.copy p{margin-bottom:16px}
.more{width:154px;height:40px;line-height:40px;font-size:13px;margin-top:8px}
.more::after{content:" \25B8"}

/* footer */
.footer{left:0;top:2900px;width:1200px;height:460px;background:var(--ink)}
.f-brand{left:110px;top:3082px;font-family:'Montserrat',sans-serif;font-weight:800;font-size:38px;color:var(--white)}
.social{left:112px;top:3150px;display:flex;gap:10px}
.social i{width:34px;height:34px;background:var(--white)}
.f-head{font-family:'Montserrat',sans-serif;font-weight:700;font-size:24px;color:var(--white)}
.f-list{list-style:none;font-size:15px;line-height:27px;color:#d7d9de}
.f-list li::before{content:"\25B8  ";color:var(--blue)}
.contact{font-size:15px;line-height:22px;color:#d7d9de}
.contact div{display:flex;gap:12px;margin-bottom:18px}
.contact svg{flex:none;margin-top:3px}
.field{width:270px;height:40px;background:var(--white);border-radius:3px;font-size:13px;color:var(--muted);padding:11px 12px}
.submit{width:110px;height:40px;line-height:40px}
.legal{left:0;top:3310px;width:1200px;height:50px;border-top:1px solid #22273a;text-align:center;font-size:14px;color:#c6c9d1;line-height:48px}
</style>
</head>
<body>

<header class="abs hero">
  <div class="abs hero-visual" role="img" aria-label="Dark blue technology backdrop with glowing circuitry"></div>
  <div class="abs hero-device" role="img" aria-label="Open laptop with a lit screen on a digital grid"></div>
  <nav class="abs nav">
    <div class="abs brand">Pellowar</div>
    <ul class="abs menu">
      <li class="active">Home</li><li>About us</li><li>Build ur product</li><li>Build your team</li><li>Case study</li>
    </ul>
    <div class="abs btn quote">Get a quote</div>
  </nav>
  <h1 class="abs hero-title">We are a <span>software</span><br><span>development</span> company</h1>
  <div class="abs btn start">Get started</div>
  <div class="abs dots"><i></i><i></i><i></i><i></i></div>
  <svg class="abs hero-wave" viewBox="0 0 1200 180" preserveAspectRatio="none"><path d="M0 120 C250 0 420 40 600 110 C800 190 1000 150 1200 40 L1200 180 L0 180Z" fill="var(--white)"/></svg>
  <div class="abs mouse"></div>
</header>

<svg class="abs band" style="top:1240px;height:560px" viewBox="0 0 1200 560" preserveAspectRatio="none"><path d="M0 60 C300 0 600 110 900 40 C1020 15 1120 20 1200 40 L1200 500 C900 560 600 450 300 520 C180 545 80 540 0 520Z" fill="var(--band)"/></svg>
<svg class="abs band" style="top:2250px;height:680px" viewBox="0 0 1200 680" preserveAspectRatio="none"><path d="M0 40 C300 110 600 0 900 60 C1020 85 1120 80 1200 60 L1200 680 L0 680Z" fill="var(--band)"/></svg>

<section>
  <div class="abs photo" style="left:100px;top:780px;width:440px;height:440px;background:linear-gradient(135deg,#9bb0c7,#3c4f66)" role="img" aria-label="Developer typing code on a laptop"></div>
  <h2 class="abs h2" style="left:740px;top:800px">About us</h2>
  <div class="abs text-block" style="left:596px;top:874px;width:460px">
    <div class="copy">
      <p>Teams are the essence of every business. They can create wonders if built with perfection.</p>
      <p>We are a group of entrepreneurs, technocrats, software architects, and delivery heads who have come together to serve startups, product companies and enterprises with their product development. We are prompt in understanding your product and help design, build, maintain and operate your product. Our teams cover UI and UX experts, Business Analysts, Developers and QA resources to build the best team to deliver the product.</p>
      <p>Businesses can focus on core activities of Sales and Marketing to achieve revenue growth, and we will accelerate your go to market.</p>
    </div>
    <div class="btn more">Learn more</div>
  </div>
</section>

<section>
  <h2 class="abs h2" style="left:130px;top:1360px">Build ur product</h2>
  <div class="abs text-block right" style="left:130px;top:1424px;width:460px">
    <div class="copy">
      <p>As startups are racing to build software as a product, they face mounting blocks on building software from scratch. One of the reasons is stiff competition.</p>
      <p>The competition to get the best resources, robust design, and scalable technology is overwhelming.</p>
      <p>Startup owners must see the CEO mindset while building a software product. Think of the bigger picture. Focus on the outcome and set aside the low technical details.</p>
    </div>
    <div class="btn more">Learn more</div>
  </div>
  <div class="abs photo" style="left:680px;top:1250px;width:460px;height:460px;background:linear-gradient(135deg,#4a5668,#11151f)" role="img" aria-label="Hands on a keyboard with glowing code graphics"></div>
</section>

<section>
  <div class="abs photo" style="left:40px;top:1790px;width:500px;height:500px;background:linear-gradient(135deg,#b9a59a,#3f4a5c)" role="img" aria-label="Team of developers working together at computers"></div>
  <h2 class="abs h2" style="left:680px;top:1886px">Build your team</h2>
  <div class="abs text-block" style="left:596px;top:1954px;width:460px">
    <div class="copy">
      <p>Break free from traditional recruiting with us. At Pellowar, we help you achieve the right organizational rhythm with a team who can take your business to the next level.</p>
      <p>We have spent years trying to innovate and improve the process of hiring talented individuals who can take businesses to the next level. We ensure that the workforce we employ for your organization is highly productive.</p>
    </div>
    <div class="btn more">Learn more</div>
  </div>
</section>

<section>
  <h2 class="abs h2" style="left:300px;top:2380px">Case study</h2>
  <div class="abs text-block right" style="left:130px;top:2446px;width:460px">
    <div class="copy">
      <p>Many business owners have great ideas but no experience with the actual product. Once you have an idea in mind, you will require software development aid at some point, whether your scenario is the next generation software or an inventive approach to offering an existing service. It might also be the development of a mobile app or web-based software. Whatever product you're working on, you'll need a technical co-founder to help you get it off the ground. An MVP can help you turn your vision into reality. An MVP is a simple, functional version of your product that can be produced quickly and cheaply.</p>
    </div>
  </div>
  <div class="abs photo" style="left:640px;top:2320px;width:520px;height:520px;background:linear-gradient(135deg,#d3d8de,#5d6a7a)" role="img" aria-label="Colleagues discussing a project around office computers"></div>
</section>

<footer>
  <svg class="abs band" style="top:2820px;height:120px" viewBox="0 0 1200 120" preserveAspectRatio="none"><path d="M0 80 C300 0 600 120 900 50 C1050 20 1130 30 1200 50 L1200 120 L0 120Z" fill="var(--ink)"/></svg>
  <div class="abs footer"></div>
  <div class="abs f-brand">Pellowar</div>
  <div class="abs social"><i></i><i></i><i></i><i></i></div>

  <h3 class="abs f-head" style="left:396px;top:3026px">Information</h3>
  <ul class="abs f-list" style="left:410px;top:3070px">
    <li>Home</li><li>Services</li><li>Features</li><li>About us</li><li>Blog</li><li>Contact us</li>
  </ul>

  <h3 class="abs f-head" style="left:576px;top:3026px">Contact Us</h3>
  <div class="abs contact" style="left:580px;top:3074px;width:200px">
    <div><svg width="12" height="16" viewBox="0 0 12 16"><path d="M6 0C2.7 0 0 2.6 0 5.9 0 10.3 6 16 6 16s6-5.7 6-10.1C12 2.6 9.3 0 6 0zm0 8a2 2 0 110-4 2 2 0 010 4z" fill="var(--blue)"/></svg><span>48 Banjara Lane,<br>Hyderabad</span></div>
    <div><svg width="14" height="14" viewBox="0 0 14 14"><path d="M3 0l2.5 3.5-1.6 1.8a9 9 0 004.8 4.8l1.8-1.6L14 11l-1.8 2.4C7 14 0 7 .6 1.8z" fill="var(--blue)"/></svg><span>+1 555 010 2040</span></div>
    <div><svg width="15" height="12" viewBox="0 0 15 12"><rect width="15" height="12" rx="1" fill="var(--blue)"/><path d="M0 1l7.5 6L15 1" stroke="var(--ink)" stroke-width="1.4" fill="none"/></svg><span>hello@pellowar.com</span></div>
  </div>

  <h3 class="abs f-head" style="left:820px;top:3026px">Newsletter</h3>
  <div class="abs field" style="left:822px;top:3076px">Name</div>
  <div class="abs field" style="left:822px;top:3124px">Email</div>
  <div class="abs btn submit" style="left:822px;top:3176px">Submit</div>

  <div class="abs legal">&copy; Copyright Pellowar 2022. All rights reserved | Privacy policy | Terms Condition</div>
</footer>

</body>
</html>
```